We need a business card design for a new company located in Brampton Ontario Canada. Our goal is to promote companies to use our service as an "External Program Management " firm taking their industrial product concepts " from prototype to production." We would like to use blue and yellow as our colors. Our skills include finding suppliers for prototype parts and developing them into supplying not only prototypes but the final production parts as well for our customer base.
Industry/Entity Type
Business
Contact Information for Business Card
Derek Namsby
Sales Manager
KOLVEN Solutions Inc.
14 Pinemarsh Lane
Brampton, Ontario L7P 2K9
Canada
Phone: 905-481-2976
Fax: 905-481-2976
website: www.kolvensolutions-example.com
Email: derek@kolvensolutions-example.com
Look and feel
Each slider illustrates characteristics of the customer's brand and the style your logo design should communicate.

```html
<!DOCTYPE html>
<html lang="en">
<head>
<meta charset="utf-8">
<title>KOLVEN Solutions Inc. – Business Card</title>
<link rel="stylesheet" href="https://fonts.googleapis.com/css2?family=Open+Sans:wght@400;600;700&display=swap">
<style>
  :root {
    --page-bg: #e9eaee;
    --card-white: #ffffff;
    --card-shade: #eeeeef;
    --brand-blue: #1518d8;
    --brand-blue-bright: #1f2cf5;
    --divider-grey: #8c8c8e;
    --text-light: #ffffff;
    --text-soft: #e3e6ff;
  }
  html, body {
    margin: 0;
    width: 1200px;
    height: 900px;
    overflow: hidden;
    background: var(--page-bg);
    font-family: "Open Sans", Arial, sans-serif;
  }
  .canvas {
    position: relative;
    width: 1200px;
    height: 900px;
  }
  .business-card {
    position: absolute;
    left: 100px;
    top: 164px;
    width: 1000px;
    height: 572px;
    border-radius: 56px;
    overflow: hidden;
    background: linear-gradient(160deg, var(--card-white) 40%, var(--card-shade));
    box-shadow: 0 18px 40px rgba(20, 24, 60, 0.18);
  }
  .card-wave {
    position: absolute;
    inset: 0;
    width: 100%;
    height: 100%;
  }
  .company-name {
    position: absolute;
    left: 110px;
    top: 66px;
    margin: 0;
    color: var(--brand-blue);
    font-weight: 700;
    line-height: 1;
  }
  .company-name .name-main {
    display: block;
    font-size: 104px;
    letter-spacing: 1px;
  }
  .company-name .name-sub {
    display: block;
    font-size: 44px;
    margin-top: 4px;
    letter-spacing: 0.5px;
  }
  .person {
    position: absolute;
    left: 64px;
    top: 412px;
    color: var(--text-light);
  }
  .person-name {
    margin: 0;
    font-size: 30px;
    font-weight: 700;
    letter-spacing: 0.5px;
  }
  .person-title {
    margin: 2px 0 0;
    font-size: 24px;
    font-weight: 400;
    color: var(--text-soft);
  }
  .contact-list {
    position: absolute;
    left: 560px;
    top: 368px;
    margin: 0;
    padding: 0;
    list-style: none;
    color: var(--text-light);
    font-size: 21px;
  }
  .contact-item {
    display: flex;
    align-items: center;
    gap: 12px;
    height: 34px;
  }
  .contact-icon {
    width: 20px;
    height: 20px;
    flex: none;
    fill: var(--text-light);
  }
</style>
</head>
<body>
<main class="canvas">
  <section class="business-card" aria-label="Business card front">
    <svg class="card-wave" viewBox="0 0 1000 572" preserveAspectRatio="none" aria-hidden="true">
      <defs>
        <linearGradient id="blueBand" x1="0" y1="1" x2="1" y2="0">
          <stop offset="0" stop-color="var(--brand-blue)"/>
          <stop offset="1" stop-color="var(--brand-blue-bright)"/>
        </linearGradient>
      </defs>
      <path d="M0,318 Q540,392 1000,112 L1000,572 L0,572 Z" fill="var(--divider-grey)"/>
      <path d="M0,334 Q545,408 1000,132 L1000,572 L0,572 Z" fill="url(#blueBand)"/>
    </svg>

    <h1 class="company-name">
      <span class="name-main">KOLVEN</span>
      <span class="name-sub">Solutions Inc.</span>
    </h1>

    <div class="person">
      <p class="person-name">DEREK NAMSBY</p>
      <p class="person-title">Sales Manager</p>
    </div>

    <ul class="contact-list">
      <li class="contact-item">
        <svg class="contact-icon" viewBox="0 0 20 20" aria-hidden="true"><path d="M6 1h8a2 2 0 0 1 2 2v14a2 2 0 0 1-2 2H6a2 2 0 0 1-2-2V3a2 2 0 0 1 2-2zm0 3v11h8V4zm4 12.2a1 1 0 1 0 0 .01z"/></svg>
        <span>905-481-2976</span>
      </li>
      <li class="contact-item">
        <svg class="contact-icon" viewBox="0 0 20 20" aria-hidden="true"><path d="M4.5 2l3 3.5-1.8 2.2a11 11 0 0 0 6.6 6.6l2.2-1.8 3.5 3-2 2.5C9 17.5 2.5 11 2 4.5z"/></svg>
        <span>905-481-2976</span>
      </li>
      <li class="contact-item">
        <svg class="contact-icon" viewBox="0 0 20 20" aria-hidden="true"><path d="M1 4h18v12H1zm1.5 1.2L10 11l7.5-5.8z"/></svg>
        <span>derek@kolvensolutions-example.com</span>
      </li>
      <li class="contact-item">
        <svg class="contact-icon" viewBox="0 0 20 20" aria-hidden="true"><path d="M10 1a9 9 0 1 0 0 18 9 9 0 0 0 0-18zm0 1.8c.9 1 1.6 2.6 1.9 4.4H8.1c.3-1.8 1-3.4 1.9-4.4zM2.9 8.9h3.5a15 15 0 0 0 0 2.2H2.9a7 7 0 0 1 0-2.2zm5 0h4.2a13 13 0 0 1 0 2.2H7.9a13 13 0 0 1 0-2.2zm5.7 0h3.5a7 7 0 0 1 0 2.2h-3.5a15 15 0 0 0 0-2.2zM8.1 12.8h3.8c-.3 1.8-1 3.4-1.9 4.4-.9-1-1.6-2.6-1.9-4.4z"/></svg>
        <span>www.kolvensolutions-example.com</span>
      </li>
      <li class="contact-item">
        <svg class="contact-icon" viewBox="0 0 20 20" aria-hidden="true"><path d="M10 1a6 6 0 0 0-6 6c0 4.5 6 12 6 12s6-7.5 6-12a6 6 0 0 0-6-6zm0 8.3a2.3 2.3 0 1 1 0-4.6 2.3 2.3 0 0 1 0 4.6z"/></svg>
        <span>14 Pinemarsh Lane, Brampton L7P 2K9</span>
      </li>
    </ul>
  </section>
</main>
</body>
</html>
```